Bramblewood Card Company Business Cards

We are a trading card store with Glimmorax, sports and other TCG cards, we need a business card design that encompasses a clean cut, modern style with a retro flare. website is bramblewoodcardco.com for reference. Can utilize a comic book era feel or a more modern outdoor feel to utilize the "Pacific Northwest" elements of tress, mountains, etc.

Industry/Entity Type

Trading cards and collectibles

Contact Information for Business Card

business name, email address, phone number, name, owner job title

Font styles to use
Sans Serif

```html
<!DOCTYPE html>
<html lang="en">
<head>
<meta charset="utf-8">
<title>Bramblewood Card Company – Business Card</title>
<link href="https://fonts.googleapis.com/css2?family=Montserrat:wght@400;500;700;800&display=swap" rel="stylesheet">
<style>
  :root {
    --stage: #262626;
    --card-white: #ffffff;
    --brand-cyan: #22bde0;
    --ink-grey: #5f5f5f;
    --rule-grey: #8a8a8a;
    --back-light: #9a9a9a;
    --back-dark: #5a5a5a;
    --back-shape: #6e6e6e;
  }
  * { box-sizing: border-box; margin: 0; padding: 0; }
  html, body {
    width: 1200px; height: 801px; overflow: hidden;
    background: var(--stage);
    font-family: "Montserrat", sans-serif;
  }
  .stage {
    position: relative; width: 1200px; height: 801px;
    display: flex; align-items: center; justify-content: center; gap: 60px;
  }
  .card {
    position: relative; width: 500px; height: 278px;
    border-radius: 16px; overflow: hidden;
  }
  /* Front */
  .card-front { background: var(--card-white); }
  .edge-band {
    position: absolute; left: 0; top: 0; bottom: 0; width: 34px;
    background: var(--brand-cyan);
  }
  .edge-rule {
    position: absolute; top: 0; bottom: 0; width: 2px; background: var(--rule-grey);
  }
  .edge-rule.one { left: 38px; }
  .edge-rule.two { left: 44px; }
  .brand-mark {
    position: absolute; left: 20px; top: 86px; width: 130px;
    padding: 10px 8px; border-radius: 8px;
    background: var(--ink-grey); color: var(--card-white);
    font-weight: 800; font-size: 13px; line-height: 1.25;
    text-transform: uppercase; letter-spacing: 0.5px; text-align: center;
  }
  .holder {
    position: absolute; right: 30px; top: 40px; text-align: right;
  }
  .holder-name {
    color: var(--brand-cyan); font-weight: 700; font-size: 22px; letter-spacing: 0.5px;
  }
  .holder-title {
    color: var(--ink-grey); font-size: 12px; margin-top: 2px;
  }
  .divider {
    position: absolute; left: 170px; right: 30px; top: 112px;
    height: 1px; background: var(--rule-grey);
  }
  .address {
    position: absolute; right: 30px; top: 132px; text-align: right;
    color: var(--ink-grey); font-size: 12px; line-height: 1.55;
  }
  .contact-list {
    position: absolute; left: 170px; bottom: 26px; list-style: none;
    color: var(--ink-grey); font-size: 12.5px; line-height: 1.8;
  }
  .contact-list li { display: flex; align-items: center; gap: 8px; }
  .contact-list svg { width: 11px; height: 11px; flex: none; }
  /* Back */
  .card-back {
    background: linear-gradient(135deg, var(--back-light), var(--back-dark));
    display: flex; align-items: center; justify-content: center;
  }
  .back-scenery {
    position: absolute; inset: 0;
    background: linear-gradient(160deg, rgba(255,255,255,0.08), rgba(0,0,0,0.06) 60%, var(--back-shape) 100%);
    opacity: 0.6;
  }
  .back-brand {
    position: relative; text-align: center; color: var(--card-white);
    font-weight: 800; font-size: 26px; line-height: 1.2;
    text-transform: uppercase; letter-spacing: 1px; width: 300px;
  }
</style>
</head>
<body>
<main class="stage">
  <section class="card card-front" aria-label="Business card front">
    <div class="edge-band"></div>
    <div class="edge-rule one"></div>
    <div class="edge-rule two"></div>
    <div class="brand-mark">Bramblewood Card Company</div>
    <div class="holder">
      <div class="holder-name">DORIAN VALE</div>
      <div class="holder-title">CEO/Founder</div>
    </div>
    <div class="divider"></div>
    <div class="address">P.O. Box 7310 Cedar Lane<br>Harbor County WA 9817</div>
    <ul class="contact-list">
      <li>
        <svg viewBox="0 0 12 12" aria-hidden="true"><path d="M2 1l2 0 1 3-1.5 1a7 7 0 0 0 3.5 3.5L8 7l3 1v2a1 1 0 0 1-1 1A9 9 0 0 1 1 2a1 1 0 0 1 1-1z" fill="var(--brand-cyan)"/></svg>
        (555) 318 2046
      </li>
      <li>
        <svg viewBox="0 0 12 12" aria-hidden="true"><rect x="0.5" y="2" width="11" height="8" fill="var(--brand-cyan)"/><path d="M0.5 2l5.5 4.5L11.5 2" fill="none" stroke="#fff" stroke-width="1"/></svg>
        info@bramblewoodcardco.com
      </li>
      <li>
        <svg viewBox="0 0 12 12" aria-hidden="true"><circle cx="6" cy="6" r="5.5" fill="var(--brand-cyan)"/><path d="M0.5 6h11M6 0.5v11M6 0.5c-3 3-3 8 0 11M6 0.5c3 3 3 8 0 11" fill="none" stroke="#fff" stroke-width="0.8"/></svg>
        www.bramblewoodcardco.com
      </li>
    </ul>
  </section>

  <section class="card card-back" aria-label="Business card back">
    <div class="back-scenery" role="img" aria-label="Faint mountain range decoration across the card back"></div>
    <div class="back-brand">Bramblewood Card Company</div>
  </section>
</main>
</body>
</html>
```